Talon Microsystems PowerPoint Master Slide Deck Design

This is a 2-phase project to design a slide deck for a semiconductor company in the Silicon Valley. The design budget will be increased with each phase.
The slide deck will need to have one version with a dark background for presentations and a second version with a white background. Otherwise, the slides will be the same. I anticipate we will need a total of 10 slides, but that number may change.
The first phase will be to design a Title and a Title and Content slide.
- The Title Slide is the first slide of the deck. It should include the presentation title, the presenter's name and date of presentation
- The Title and Content slide should include a title and content with bullet points and up to 2 additional sub-bullets
- The Title and Content slide should have a footer that includes the slide #, Talon Microsystems Confidential, and the logo. This footer will be on every slide except the Title Slide
The first two slides will serve as the format for the remaining ~8 slides:
-Header and Content Text (1, 2, 4 column)
-Header and Content Image (bar chart, pie chart, tables)
-Break
-Title only
-Closing (Talon logo only)
Our slides contain a lot of content so a clean and simple design is best.
Both phases will need to include pre-set color options for
-Text and Lines
-Shadows
-Bullets and sub-bullets (including shapes, ex. circle, slash, square, etc.)
-Bar charts, pie charts, tables
Samples of our collateral are attached. Logo files are also attached
Look and feel
Each slider illustrates characteristics of the customer's brand and the style your logo design should communicate.

```html
<!DOCTYPE html>
<html lang="en">
<head>
<meta charset="utf-8">
<title>Talon Microsystems Slide Deck</title>
<link rel="stylesheet" href="https://fonts.googleapis.com/css2?family=Roboto:wght@400;500;700;900&display=swap">
<style>
  :root{
    --blue:#0b53a8;
    --blue-dark:#0a4a96;
    --blue-page:#1a66bf;
    --blue-bright:#1464d8;
    --pale:#cfe0f1;
    --text:#1f2430;
    --muted:#3a3f4a;
    --teal:#17a58c;
    --page-bg:#ffffff;
  }
  *{margin:0;padding:0;box-sizing:border-box}
  html,body{width:1200px;height:4065px;overflow:hidden;background:var(--page-bg)}
  body{position:relative;font-family:"Roboto",Arial,sans-serif;color:var(--text)}
  .slide{position:absolute;left:77px;width:1036px;height:585px;background:#fff;overflow:hidden;
    box-shadow:0 6px 18px rgba(0,0,0,.18)}
  .footer{position:absolute;left:0;bottom:0;width:100%;height:55px;background:var(--blue);color:#fff;
    display:flex;align-items:center;font-size:12px;letter-spacing:.2px}
  .footer .conf{position:absolute;left:45px}
  .footer .brand{position:absolute;left:50%;transform:translateX(-50%);display:flex;align-items:center;gap:6px;font-size:13px;font-weight:500}
  .footer .page{position:absolute;right:0;top:0;height:100%;width:147px;background:var(--blue-page);
    display:flex;align-items:center;justify-content:center;font-weight:500}
  .dot{display:inline-block;border-radius:50%;background:currentColor}
  .h2{font-weight:700;color:var(--blue);font-size:25px;letter-spacing:.2px}
  .rule{width:66px;height:3px;background:var(--blue);margin-top:4px}
  .small{font-size:10.5px;line-height:18px;color:var(--muted)}
  /* slide 1 */
  .s1{top:73px;border-top:5px solid var(--blue);border-bottom:5px solid var(--blue)}
  .s1 .bg{position:absolute;inset:0;background:radial-gradient(ellipse at 50% 55%,#c9b79a 0%,#9fa9b4 35%,#a9b4c2 70%,#bfc7d2 100%)}
  .s1 .veil{position:absolute;inset:0;background:rgba(225,230,238,.55)}
  .s1 .center{position:absolute;left:0;right:0;top:112px;text-align:center}
  .s1 .brandline{display:flex;justify-content:center;align-items:center;gap:12px;font-size:34px;font-weight:500;color:var(--blue-dark)}
  .s1 h1{margin-top:28px;font-size:42px;line-height:52px;font-weight:700;color:var(--blue)}
  .s1 .sub{margin-top:14px;font-size:12px;color:var(--muted)}
  .s1 .name{margin-top:14px;font-size:14px;font-weight:500;color:var(--text)}
  .s1 .date{display:inline-flex;align-items:center;gap:6px;margin-top:14px;background:var(--teal);color:#fff;font-size:10.5px;padding:5px 16px;border-radius:14px}
  /* slide 2 */
  .s2{top:731px}
  .s2 .title{position:absolute;left:43px;top:83px}
  .s2 .cols{position:absolute;left:43px;top:142px;width:950px;display:grid;grid-template-columns:1fr 1fr;column-gap:40px;row-gap:22px}
  .bul{list-style:none}
  .bul li{position:relative;padding-left:16px;font-size:10.8px;line-height:18px;color:var(--muted)}
  .bul li::before{content:"";position:absolute;left:2px;top:5px;border-left:7px solid var(--blue);border-top:4px solid transparent;border-bottom:4px solid transparent}
  .bul ul{list-style:none;margin:8px 0 0 22px}
  .bul ul li{margin-bottom:8px}
  .bul ul li::before{border-left-color:#4f86cc}
  /* slide 3 */
  .s3{top:1391px}
  .s3 .hero{position:absolute;left:0;top:0;width:100%;height:292px;background:linear-gradient(120deg,#1b1c22 0%,#3a3128 35%,#5c4a2f 55%,#1f2a36 80%,#121419 100%)}
  .s3 .hero-text{position:absolute;left:0;right:0;top:108px;text-align:center;color:#fff}
  .s3 .hero-text h2{font-size:25px;font-weight:700}
  .s3 .hero-text .rule{background:#fff;margin:4px auto 0}
  .s3 .hero-text p{margin-top:14px;font-size:13.5px;line-height:20px}
  .s3 .feature{position:absolute;top:245px;width:280px;text-align:center}
  .s3 .icon{width:94px;height:94px;margin:0 auto;border-radius:50%;background:var(--blue);border:3px solid #fff;display:flex;align-items:center;justify-content:center}
  .s3 .feature p{margin-top:26px;font-size:10.5px;line-height:19px;color:var(--muted)}
  /* slide 4 */
  .s4{top:2050px}
  .tile{position:absolute;width:260px;height:258px}
  .tile.text{background:var(--pale);padding:18px 28px 0 32px;font-size:10.3px;line-height:20.6px;color:var(--muted)}
  .s4 .right{position:absolute;left:560px;top:65px;width:440px}
  .s4 .right p{margin-top:14px;font-size:10.3px;line-height:20.6px;color:var(--muted)}
  /* slide 5 */
  .s5{top:2708px}
  .s5 .left{position:absolute;left:43px;top:68px;width:460px}
  .s5 .left p{margin-top:14px;font-size:12px;line-height:21.7px;color:var(--muted)}
  .photo-circle{position:absolute;border-radius:50%;border:4px solid #1aa08c}
  /* slide 6 */
  .s6{top:3367px;border-top:5px solid var(--blue);border-bottom:5px solid var(--blue)}
  .s6 .closing{position:absolute;left:0;right:0;top:230px;display:flex;justify-content:center;align-items:center;gap:18px;font-size:60px;font-weight:500;color:var(--blue-dark)}
</style>
</head>
<body>

<!-- Title slide -->
<section class="slide s1">
  <div class="bg" role="img" aria-label="Close-up photo of a processor chip on a circuit board"></div>
  <div class="veil"></div>
  <div class="center">
    <div class="brandline"><span class="dot" style="width:26px;height:26px"></span>Talon Microsystems</div>
    <h1>TALON<br>MICROSYSTEMS</h1>
    <p class="sub">Lorem ipsum dolor sit amet, consectetur adipiscing elit</p>
    <p class="name">Alex</p>
    <span class="date">
      <svg width="10" height="10" viewBox="0 0 10 10"><rect x="1" y="2" width="8" height="7" fill="none" stroke="#fff" stroke-width="1"/><line x1="1" y1="4" x2="9" y2="4" stroke="#fff"/></svg>
      04/10/2023</span>
  </div>
</section>

<!-- About us -->
<section class="slide s2">
  <div class="title"><h2 class="h2">ABOUT US</h2><div class="rule"></div></div>
  <div class="cols">
    <ul class="bul"><li>Lorem ipsum dolor sit amet, consectetur adipiscing elit, sed do eiusmod tempor incididunt ut labore et dolore magna aliqua. Ut enim ad Lorem ipsum dolor sit amet, consectetur adipiscing elit, sed do eiusmod tempor incididunt ut labore
      <ul><li>Lorem ipsum dolor sit amet, consectetur adipiscing elit, sed do eiusmod tempor incididunt ut labore et dolore magna aliqua. Ut enim ad minim veniam,</li>
      <li>Lorem ipsum dolor sit amet, consectetur adipiscing elit, sed do eiusmod tempor incididunt ut labore et dolore magna aliqua. Ut enim ad minim veniam,</li></ul></li></ul>
    <ul class="bul"><li>Lorem ipsum dolor sit amet, consectetur adipiscing elit, sed do eiusmod tempor incididunt ut labore et dolore magna aliqua. Ut enim ad Lorem ipsum dolor sit amet, consectetur adipiscing elit, sed do eiusmod tempor incididunt ut labore
      <ul><li>Lorem ipsum dolor sit amet, consectetur adipiscing elit, sed do eiusmod tempor incididunt ut labore et dolore magna aliqua. Ut enim ad minim veniam,</li>
      <li>Lorem ipsum dolor sit amet, consectetur adipiscing elit, sed do eiusmod tempor incididunt ut labore et dolore magna aliqua. Ut enim ad minim veniam,</li></ul></li></ul>
    <ul class="bul"><li>Lorem ipsum dolor sit amet, consectetur adipiscing elit, sed do eiusmod tempor incididunt ut labore et dolore magna aliqua. Ut enim ad Lorem ipsum dolor sit amet, consectetur adipiscing elit, sed do eiusmod tempor incididunt ut labore
      <ul><li>Lorem ipsum dolor sit amet, consectetur adipiscing elit, sed do eiusmod tempor incididunt ut labore et dolore magna aliqua. Ut enim ad minim veniam,</li>
      <li>Lorem ipsum dolor sit amet, consectetur adipiscing elit, sed do eiusmod tempor incididunt ut labore et dolore magna aliqua. Ut enim ad minim veniam,</li></ul></li></ul>
    <ul class="bul"><li>Lorem ipsum dolor sit amet, consectetur adipiscing elit, sed do eiusmod tempor incididunt ut labore et dolore magna aliqua. Ut enim ad Lorem ipsum dolor sit amet, consectetur adipiscing elit, sed do eiusmod tempor incididunt ut labore
      <ul><li>Lorem ipsum dolor sit amet, consectetur adipiscing elit, sed do eiusmod tempor incididunt ut labore et dolore magna aliqua. Ut enim ad minim veniam,</li>
      <li>Lorem ipsum dolor sit amet, consectetur adipiscing elit, sed do eiusmod tempor incididunt ut labore et dolore magna aliqua. Ut enim ad minim veniam,</li></ul></li></ul>
  </div>
  <footer class="footer"><span class="conf">TALON MICROSYSTEMS CONFIDENTIAL</span><span class="brand"><span class="dot" style="width:10px;height:10px"></span>Talon Microsystems</span><span class="page">PAGE | 02</span></footer>
</section>

<!-- What we do -->
<section class="slide s3">
  <div class="hero" role="img" aria-label="Dark photo of a microchip on a circuit board"></div>
  <div class="hero-text">
    <h2>WHAT WE DO</h2><div class="rule"></div>
    <p>Lorem ipsum dolor sit amet, consectetur adipiscing elit, sed do<br>eiusmod tempor incididunt ut labore et dolore magna aliqua.</p>
  </div>
  <div class="feature" style="left:28px">
    <div class="icon"><svg width="36" height="36" viewBox="0 0 36 36" fill="none" stroke="#fff" stroke-width="1.6"><rect x="8" y="8" width="20" height="20"/><rect x="13" y="13" width="10" height="10"/><path d="M12 4v4M18 4v4M24 4v4M12 28v4M18 28v4M24 28v4M4 12h4M4 18h4M4 24h4M28 12h4M28 18h4M28 24h4"/></svg></div>
    <p>Lorem ipsum dolor sit amet, consectetur adipiscing elit, sed do eiusmod tempor incididunt ut labore et dolore magna aliqua. Ut enim ad minim veniam, quis nostrud exercitation ullamco laboris nisi ut aliquip ex ea commodo consequat.</p>
  </div>
  <div class="feature" style="left:378px">
    <div class="icon"><svg width="36" height="36" viewBox="0 0 36 36" fill="none" stroke="#fff" stroke-width="1.6"><rect x="10" y="5" width="16" height="26" rx="1"/><path d="M14 10h8M14 14h8M18 25v2"/></svg></div>
    <p>Lorem ipsum dolor sit amet, consectetur adipiscing elit, sed do eiusmod tempor incididunt ut labore et dolore magna aliqua. Ut enim ad minim veniam, quis nostrud exercitation ullamco laboris nisi ut aliquip ex ea commodo consequat.</p>
  </div>
  <div class="feature" style="left:728px">
    <div class="icon"><svg width="38" height="36" viewBox="0 0 38 36" fill="none" stroke="#fff" stroke-width="1.6"><path d="M19 8l14 8-14 8-14-8z"/><path d="M19 13l6 3-6 3-6-3z"/><path d="M5 16v4l14 8 14-8v-4"/></svg></div>
    <p>Lorem ipsum dolor sit amet, consectetur adipiscing elit, sed do eiusmod tempor incididunt ut labore et dolore magna aliqua. Ut enim ad minim veniam, quis nostrud exercitation ullamco laboris nisi ut aliquip ex ea commodo consequat.</p>
  </div>
  <footer class="footer"><span class="conf">TALON MICROSYSTEMS CONFIDENTIAL</span><span class="brand"><span class="dot" style="width:10px;height:10px"></span>Talon Microsystems</span><span class="page">PAGE | 03</span></footer>
</section>

<!-- Semiconductor -->
<section class="slide s4">
  <div class="tile" style="left:0;top:0;background:linear-gradient(135deg,#8fb4d9,#3d6f9e 50%,#c7d9ea)" role="img" aria-label="Photo of a clean-room chip fabrication machine"></div>
  <div class="tile text" style="left:260px;top:0">Lorem ipsum dolor sit amet, consectetur adipiscing elit, sed do eiusmod tempor incididunt ut labore et dolore magna aliqua. Ut enim ad minim veniam, quis nostrud exercitation ullamco laboris nisi ut aliquip ex ea commodo consequat.Lorem ipsum dolor sit amet, consectetur adipiscing elit, sed do eiusmod tempor incididunt ut labore et</div>
  <div class="tile text" style="left:0;top:258px">Lorem ipsum dolor sit amet, consectetur adipiscing elit, sed do eiusmod tempor incididunt ut labore et dolore magna aliqua. Ut enim ad minim veniam, quis nostrud exercitation ullamco laboris nisi ut aliquip ex ea commodo consequat.Lorem ipsum dolor sit amet, consectetur adipiscing elit, sed do eiusmod tempor incididunt ut labore et</div>
  <div class="tile" style="left:260px;top:258px;height:272px;background:linear-gradient(160deg,#2a1f2e,#a83a4a 45%,#1d4f73 80%,#0f1a28)" role="img" aria-label="Photo of a wafer inspection tool over a chip"></div>
  <div class="right">
    <h2 class="h2">SEMICONDUCTOR</h2><div class="rule"></div>
    <p>Lorem ipsum dolor sit amet, consectetur adipiscing elit, sed do eiusmod tempor incididunt ut labore et dolore magna aliqua. Ut enim ad minim veniam, quis nostrud exercitation ullamco laboris nisi ut aliquip ex ea commodo consequat. Duis aute irure dolor in reprehenderit in voluptate velit esse cillum dolore eu fugiat nulla pariatur. Excepteur sint occaecat cupidatat non proident, sunt in culpa qui officia deserunt mollit anim id est laborum.Lorem ipsum dolor sit amet, consectetur adipiscing elit, sed do eiusmod tempor incididunt ut labore et dolore magna aliqua. Ut enim ad minim veniam, quis nostrud exercitation ullamco laboris nisi ut aliquip ex ea commodo consequat. Duis aute irure dolor in reprehenderit in voluptate velit esse cillum dolore eu fugiat nulla pariatur. Excepteur sint occaecat cupidatat non proident, sunt in culpa qui officia deserunt mollit anim id est laborum.Lorem ipsum dolor sit amet, consectetur adipiscing elit, sed do eiusmod tempor incididunt ut labore et dolore magna aliqua. Ut enim ad minim veniam, quis nostrud exercitation ullamco laboris nisi ut aliquip ex ea commodo consequat. Duis aute irure dolor in reprehenderit in voluptate velit esse cillum dolore eu fugiat nulla pariatur. Excepteur sint occaecat cupidatat non proident, sunt in culpa qui officia deserunt mollit anim id est laborum.Lorem ipsum dolor sit amet, consectetur adipiscing elit, sed do eiusmod tempor incididunt ut labore et dolore magna aliqua. Ut enim ad minim veniam, quis nostrud exercitation ullamco laboris nisi</p>
  </div>
  <footer class="footer"><span class="conf">TALON MICROSYSTEMS CONFIDENTIAL</span><span class="brand"><span class="dot" style="width:10px;height:10px"></span>Talon Microsystems</span><span class="page">PAGE | 04</span></footer>
</section>

<!-- Company detail -->
<section class="slide s5">
  <div class="left">
    <h2 class="h2">TALON MICROSYSTEMS</h2>
    <p>Lorem ipsum dolor sit amet, consectetur adipiscing elit, sed do eiusmod tempor incididunt ut labore et dolore magna aliqua. Ut enim ad minim veniam, quis nostrud exercitation ullamco laboris nisi ut aliquip ex ea commodo consequat. Duis aute irure dolor in reprehenderit in voluptate velit esse cillum dolore eu fugiat nulla pariatur. Excepteur sint occaecat cupidatat non proident, sunt in culpa qui officia deserunt mollit anim id est laborum.Lorem ipsum dolor sit amet, consectetur adipiscing elit, sed do eiusmod tempor incididunt ut labore et dolore magna aliqua. Ut enim ad minim veniam, quis nostrud exercitation ullamco laboris nisi ut aliquip ex ea commodo consequat. Duis aute irure dolor in reprehenderit in voluptate velit esse cillum dolore eu fugiat nulla pariatur. Excepteur sint occaecat cupidatat non proident, sunt in culpa qui officia deserunt mollit anim id est laborum.Lorem ipsum dolor sit amet, consectetur adipiscing elit, sed do eiusmod tempor incididunt ut labore et dolore magna aliqua. Ut enim ad minim veniam, quis nostrud exercitation ullamco laboris nisi ut aliquip ex ea commodo consequat.</p>
  </div>
  <div class="photo-circle" style="left:746px;top:72px;width:248px;height:248px;background:radial-gradient(circle,#2fd6a8 0%,#0f5a4c 40%,#15201f 80%)" role="img" aria-label="Photo of a glowing green microchip on a board"></div>
  <div class="photo-circle" style="left:550px;top:285px;width:218px;height:218px;background:radial-gradient(circle at 55% 60%,#ffd27a 0%,#d77a1e 25%,#4a3a35 60%,#1d2430 100%)" role="img" aria-label="Photo of a machine head heating a chip"></div>
  <footer class="footer"><span class="conf">TALON MICROSYSTEMS CONFIDENTIAL</span><span class="brand"><span class="dot" style="width:10px;height:10px"></span>Talon Microsystems</span><span class="page">PAGE | 05</span></footer>
</section>

<!-- Closing -->
<section class="slide s6">
  <div class="closing"><span class="dot" style="width:56px;height:56px"></span>Talon Microsystems</div>
</section>

</body>
</html>
```